Real Estate stationery - need an interesting, eye catching design

I need a letterhead and #10 envelope design in the same theme.
I am looking for an interesting, eye catching design that would stand out in the crowd. I am in the real estate business(which is very competitive) in Florida so standing out and being different is very important to me.
Marguerite(Rita) Delacourt (name), RealtorĀ® (title), 352-608-2147 (cell), bayviewritahomes@quellmail.com (email), www.bayviewritahomes.com(website), 915 Calloway Creek Blvd.,Ste. 3140, Longwood, FL 32779 (business address)

```html
<!DOCTYPE html>
<html lang="en">
<head>
<meta charset="utf-8">
<title>Bayview Homes Stationery</title>
<link href="https://fonts.googleapis.com/css2?family=Roboto:wght@300;400&display=swap" rel="stylesheet">
<style>
  :root {
    --bg: #dddddd;
    --paper: #ffffff;
    --paper-edge: #f3f3f3;
    --brown: #835b27;
    --brown-dark: #7a5425;
    --ink: #5a5a5a;
    --ink-soft: #6d6d6d;
    --rule: #c9c9c9;
  }
  * { margin: 0; padding: 0; box-sizing: border-box; }
  html, body { width: 1200px; height: 843px; overflow: hidden; }
  body {
    position: relative;
    background: var(--bg);
    font-family: "Roboto", Arial, sans-serif;
    color: var(--ink);
  }
  .sheet {
    position: absolute;
    background: linear-gradient(90deg, var(--paper-edge), var(--paper) 40%);
    box-shadow: 0 4px 14px rgba(0,0,0,.18);
    overflow: hidden;
  }
  .letterhead { left: 74px; top: 61px; width: 508px; height: 715px; }
  .envelope-back { left: 621px; top: 276px; width: 511px; height: 232px; }
  .envelope-front { left: 621px; top: 543px; width: 511px; height: 232px; }

  .brand {
    position: absolute;
    display: flex;
    align-items: center;
    gap: 6px;
    font-weight: 400;
    color: var(--brown);
    white-space: nowrap;
  }
  .brand-mark { width: 9px; height: 9px; background: var(--brown); }

  .letterhead .brand { left: 45px; top: 92px; font-size: 17px; }
  .contact-rule {
    position: absolute; left: 344px; top: 62px; width: 1px; height: 55px;
    background: var(--rule);
  }
  .contact {
    position: absolute; left: 354px; top: 64px;
    font-size: 7px; line-height: 9px; color: var(--ink); font-style: normal;
  }
  .contact .line-gap { margin-top: 4px; }
  .contact .icon { display: inline-block; vertical-align: -1px; margin-right: 3px; }
  .contact .accent { color: var(--brown-dark); }

  .salutation {
    position: absolute; left: 45px; top: 207px;
    font-size: 13px; font-weight: 300; color: #444;
  }
  .body-copy {
    position: absolute; left: 45px; top: 241px; width: 422px;
    font-size: 7.4px; line-height: 11px; font-weight: 300; color: var(--ink-soft);
    text-align: justify;
  }
  .body-copy p + p { margin-top: 11px; }
  .closing {
    position: absolute; left: 45px; top: 472px;
    font-size: 7px; font-weight: 300; color: var(--ink-soft);
  }
  .signature {
    position: absolute; left: 40px; top: 498px; width: 89px; height: 38px;
    background: linear-gradient(90deg, rgba(131,91,39,.18), rgba(131,91,39,.08));
    border-radius: 4px;
  }
  .band { position: absolute; left: 0; bottom: 0; width: 100%; display: block; }
  .letterhead .band { height: 90px; }
  .website {
    position: absolute; left: 350px; top: 683px;
    font-size: 7px; letter-spacing: 1.6px; color: #fff;
  }

  .flap { position: absolute; left: 0; top: 0; width: 100%; height: 71px; display: block; }
  .envelope-back .brand {
    left: 0; right: 0; top: 26px; justify-content: center;
    color: #fff; font-size: 14px;
  }
  .envelope-back .brand-mark { background: #fff; }

  .envelope-front .brand { left: 26px; top: 28px; font-size: 15px; }
  .return-address {
    position: absolute; left: 24px; top: 75px; width: 118px;
    font-size: 7px; line-height: 8.5px; text-align: center; color: #333; font-style: normal;
  }
  .envelope-front .band { height: 89px; }
</style>
</head>
<body>

  <section class="sheet letterhead" aria-label="Letterhead">
    <div class="brand"><span class="brand-mark"></span>Bayview Homes</div>
    <div class="contact-rule"></div>
    <address class="contact">
      915 Calloway Creek Blvd.,<br>Ste. 3140<br>Oakmere, FL 32806
      <div class="line-gap">
        <svg class="icon" width="5" height="7" viewBox="0 0 5 7"><rect x="0.5" y="0.5" width="4" height="6" rx="0.8" fill="none" stroke="#835b27"/></svg><span class="accent">352-608-2147</span>
      </div>
      <div>
        <svg class="icon" width="7" height="5" viewBox="0 0 7 5"><rect width="7" height="5" fill="#835b27"/><path d="M0 0l3.5 2.8L7 0" fill="none" stroke="#fff" stroke-width=".7"/></svg><span class="accent">bayviewritahomes@quellmail.com</span>
      </div>
    </address>

    <p class="salutation">Dear Mr. Hale,</p>
    <div class="body-copy">
      <p>Lorem ipsum dolor sit amet, consectetur adipiscing elit. Donec orci purus, luctus vitae dignissim eu, iaculis sed purus. Vivamus faucibus, ipsum nec aliquet viverra, leo mauris condimentum ligula, sit amet sagittis enim ligula quis arcu. Nam egestas tortor id nisi porttitor mattis. In tortor ante, ultricies in suscipit a, tempus non massa. Vivamus et auctor mi. Fusce vel massa nulla. Phasellus nec eros mauris, et scelerisque orci.</p>
      <p>Donec malesuada orci vitae nulla accumsan porta a id massa. Quisque accumsan iaculis magna sit amet fringilla. Maecenas consequat, magna eget tincidunt semper, odio nibh rutrum mi, id feugiat ante nisi eu risus. Vestibulum nunc orci, rhoncus a placerat in, ultricies in mi. Cras mattis varius eros, vel fringilla nisi suscipit eget. Quisque scelerisque sagittis nulla at porttitor.</p>
      <p>Sed id augue vitae urna euismod commodo aliquet a quam. Pellentesque arcu velit, cursus et malesuada ut, consequat et diam. Nullam erat sem, rhoncus id ullamcorper vitae, rhoncus et arcu. In ultricies ultricies nulla, ut rutrum nisi iaculis at. Donec eu magna a metus ornare faucibus. Fusce aliquet faucibus ultricies. Morbi semper, est id tincidunt gravida, sem arcu adipiscing lacus, ac bibendum nulla leo eu purus. Quisque nec diam sed risus consectetur accumsan quis quis nibh. Vestibulum id purus lorem.</p>
      <p>It is a long established fact that a reader will be distracted by the readable content of a page when looking at its layout. The point of using Lorem Ipsum is that it has a more-or-less normal distribution of letters, as opposed to using 'Content here, content here', making it look like readable English. Many desktop publishing packages</p>
    </div>
    <p class="closing">Sincerely,</p>
    <div class="signature" role="img" aria-label="Handwritten signature of Owen Hale"></div>

    <svg class="band" viewBox="0 0 508 90" preserveAspectRatio="none" aria-hidden="true">
      <polygon points="0,90 508,0 508,90" fill="#835b27"/>
    </svg>
    <div class="website">www.bayviewritahomes.com</div>
  </section>

  <section class="sheet envelope-back" aria-label="Envelope back">
    <svg class="flap" viewBox="0 0 511 71" preserveAspectRatio="none" aria-hidden="true">
      <path d="M0 0H511L500 40Q491 71 465 71H46Q20 71 11 40Z" fill="#7a5425"/>
    </svg>
    <div class="brand"><span class="brand-mark"></span>Bayview Homes</div>
  </section>

  <section class="sheet envelope-front" aria-label="Envelope front">
    <div class="brand"><span class="brand-mark"></span>Bayview Homes</div>
    <address class="return-address">915 Calloway Creek Blvd.,Ste. 3140<br>Oakmere, FL 32806</address>
    <svg class="band" viewBox="0 0 511 89" preserveAspectRatio="none" aria-hidden="true">
      <polygon points="0,89 511,0 511,89" fill="#835b27"/>
    </svg>
  </section>

</body>
</html>
```